Velora Entertainment

Logo for business card design

Target Market(s)

potential film investors and screenwriters

Industry/Entity Type

Business

Contact Information for Business Card

as shown, website here is a placeholder position

Requirements
Must have
• great visual appeal
Nice to have
• harmony of colors; must evoke spirit of
• U.S.-China cooperation

```html
<!DOCTYPE html>
<html lang="en">
<head>
<meta charset="utf-8">
<title>Velora Entertainment – Business Card</title>
<link rel="stylesheet" href="https://fonts.googleapis.com/css2?family=Source+Sans+3:wght@400;600;700&display=swap">
<style>
  :root {
    --page-bg: #e7e5e2;
    --card-face: #f4f5f6;
    --card-edge: #d6d8db;
    --brand-red: #d8232f;
    --brand-yellow: #f2b713;
    --brand-navy: #1b1d6b;
    --title-navy: #1f2a6e;
    --name-red: #b5121b;
    --band-text: #f3e6e6;
    --navy-text: #c9cbe6;
  }
  * { box-sizing: border-box; margin: 0; padding: 0; }
  html, body {
    width: 1200px;
    height: 969px;
    overflow: hidden;
    background: var(--page-bg);
    font-family: "Source Sans 3", "Helvetica Neue", Arial, sans-serif;
  }
  .card {
    position: absolute;
    left: 100px;
    top: 200px;
    width: 1000px;
    height: 568px;
    background: var(--card-face);
    border: 1px solid var(--card-edge);
    box-shadow: 0 18px 40px rgba(0,0,0,0.12);
    overflow: hidden;
  }
  .brand {
    position: absolute;
    left: 58px;
    top: 100px;
    display: flex;
    align-items: center;
    gap: 18px;
  }
  .brand-square {
    width: 64px;
    height: 64px;
    background: var(--brand-red);
  }
  .brand-name {
    font-weight: 700;
    font-size: 40px;
    line-height: 1;
    color: var(--brand-navy);
  }
  .person {
    position: absolute;
    right: 55px;
    top: 56px;
    text-align: right;
  }
  .person-name {
    font-weight: 600;
    font-size: 34px;
    color: var(--name-red);
    line-height: 1.1;
  }
  .person-title {
    font-weight: 400;
    font-size: 27px;
    color: var(--title-navy);
    line-height: 1.2;
  }
  .band {
    position: absolute;
    top: 372px;
    height: 196px;
  }
  .band-red { left: 0; width: 424px; background: var(--brand-red); }
  .band-yellow { left: 430px; width: 142px; background: var(--brand-yellow); }
  .band-navy { left: 578px; width: 422px; background: var(--brand-navy); }
  .contact-list {
    list-style: none;
    position: absolute;
    left: 58px;
    top: 40px;
    color: var(--band-text);
    font-size: 25px;
    line-height: 38px;
  }
  .contact-list li { display: flex; align-items: center; gap: 14px; }
  .contact-list svg { width: 22px; height: 22px; fill: var(--band-text); }
  .address {
    position: absolute;
    right: 58px;
    top: 40px;
    text-align: right;
    color: var(--navy-text);
    font-size: 25px;
    line-height: 38px;
    font-style: normal;
  }
</style>
</head>
<body>
  <div class="card">
    <div class="brand">
      <div class="brand-square"></div>
      <div class="brand-name">Velora Entertainment</div>
    </div>

    <div class="person">
      <div class="person-name">Daniel Reyes</div>
      <div class="person-title">CEO/Founder</div>
    </div>

    <div class="band band-red">
      <ul class="contact-list">
        <li>
          <svg viewBox="0 0 24 24" aria-hidden="true"><path d="M6.6 10.8a15.1 15.1 0 0 0 6.6 6.6l2.2-2.2a1 1 0 0 1 1-.25 11.4 11.4 0 0 0 3.6.57 1 1 0 0 1 1 1V20a1 1 0 0 1-1 1A17 17 0 0 1 3 4a1 1 0 0 1 1-1h3.5a1 1 0 0 1 1 1c0 1.25.2 2.45.57 3.6a1 1 0 0 1-.25 1z"/></svg>
          <span>512 804 3319</span>
        </li>
        <li>
          <svg viewBox="0 0 24 24" aria-hidden="true"><path d="M7 1h10a2 2 0 0 1 2 2v18a2 2 0 0 1-2 2H7a2 2 0 0 1-2-2V3a2 2 0 0 1 2-2zm0 3v15h10V4zm5 16.2a1 1 0 1 0 0 2 1 1 0 0 0 0-2z"/></svg>
          <span>512 706 4482</span>
        </li>
        <li>
          <svg viewBox="0 0 24 24" aria-hidden="true"><path d="M2 5h20v14H2zm2 2v.5l8 5 8-5V7zm0 2.9V17h16V9.9l-8 5z"/></svg>
          <span>hello@veloraent.com</span>
        </li>
      </ul>
    </div>
    <div class="band band-yellow"></div>
    <div class="band band-navy">
      <address class="address">
        214 Larkspur Avenue<br>
        Austin, Texas 78704<br>
        www.veloraent.com
      </address>
    </div>
  </div>
</body>
</html>
```